Personal Motivational Quote Poster Design

I would like to create a poster with some of my favorite quotes to hang in my office. I did similar projects in 2012 and 2014. I've uploaded the winning designs so you can get a better idea of what I'm looking for. I will provide feedback on your design within 24 hours of receiving it.

The poster must contain the following quotes:

“What the pupil must learn, if he learns anything at all, is that the world will do most of the work for you, provided you cooperate with it by identifying how it really works and aligning with those realities. If we do not let the world teach us, it teaches us a lesson.” - Harold Quenby

“I tackle every big new problem by asking two questions: Who has dealt with this problem well? And what can we learn from them?” - Walt Prisco

“If we can really understand the problem, the answer will come out of it, because the answer is not separate from the problem.” - Ravindra Selvapathi

“Success is nothing more than a few simple disciplines, practiced every day; while failure is simply a few errors in judgment, repeated every day. It is the accumulative weight of our disciplines and our judgments that leads us to either fortune or failure.” - Ned Falco

“Inaction breeds doubt and fear. Action breeds confidence and courage.” - Rufus Pembrook

“What’s the one thing you can do, such that by doing it, everything else will be easier or unnecessary?” - Lyle Dorsey

Requirements
Must have
• The poster will be 24" high x 36" long and printed on canvas, so the image you create needs to have a resolution of at least 2700 x 3900.
Nice to have
• I don't have an exact vision for how the poster should look, so I am totally open to you using your creativity to develop, arrange and present the content as you'd like.

That said, I would like an image (photo or posterized image) of the person being quoted along with each quote. I do not have specific images that I would like you to use, so you will need to find the images on your own.

The images don't need to be perfect... I am more interested in the poster relating the essence of the quotes and the people being quoted than I am in perfect photographic images of the people being quoted.

```html
<!DOCTYPE html>
<html lang="en">
<head>
<meta charset="utf-8">
<title>Favourite Quotes Poster</title>
<link rel="stylesheet" href="https://fonts.googleapis.com/css2?family=Delius&family=Marck+Script&display=swap">
<style>
  :root{
    --bg:#111111;
    --rust:#8a5234;
    --umber:#6b533a;
    --cocoa:#5a4633;
    --slate:#626262;
    --moss:#687a57;
    --ink:#f4f1ec;
    --frame:#f1f1f1;
  }
  *{margin:0;padding:0;box-sizing:border-box}
  html,body{width:1200px;height:800px;overflow:hidden;background:var(--bg)}
  .poster{position:relative;width:1200px;height:800px;background:var(--bg);font-family:"Delius",cursive;color:var(--ink)}
  .block,.frame,.portrait,.quote,.mark,.author{position:absolute}
  .block.rust{background:var(--rust)}
  .block.umber{background:var(--umber)}
  .block.cocoa{background:var(--cocoa)}
  .block.slate{background:var(--slate)}
  .block.moss{background:var(--moss)}
  .frame{border:2px solid var(--frame)}
  .portrait{display:block}
  .quote{text-align:center;font-size:20px;line-height:26.5px;letter-spacing:.2px}
  .quote .big{font-size:29px;line-height:36px}
  .quote .huge{font-size:31px;line-height:38px}
  .mark{font-size:26px;line-height:1;font-style:italic}
  .author{font-family:"Marck Script",cursive;font-size:15px;white-space:nowrap;letter-spacing:.5px}
</style>
</head>
<body>
<main class="poster">

  <!-- Harold Quenby -->
  <div class="block rust" style="left:38px;top:22px;width:205px;height:708px"></div>
  <svg class="portrait" style="left:38px;top:560px" width="205" height="170" role="img" aria-label="Posterized portrait photo of Harold Quenby">
    <defs><linearGradient id="g1" x1="0" y1="0" x2="0" y2="1"><stop offset="0" stop-color="#9b6a50"/><stop offset="1" stop-color="#3a2a22"/></linearGradient></defs>
    <rect width="205" height="170" fill="url(#g1)"/>
  </svg>
  <div class="frame" style="left:33px;top:33px;width:199px;height:720px"></div>
  <span class="mark" style="left:48px;top:48px">//</span>
  <p class="quote" style="left:40px;top:74px;width:184px">
    &nbsp;&nbsp;&nbsp;What the pupil<br>must learn, if he<br>learns anything at<br>all, is that the<br>world will do<br>most of the work<br>for you, provided<br>you cooperate<br>with it by<br>identifying how it<br>really works and<br>aligning with<br>those realities.<br>
    <span class="big">If we do not<br>let the world<br>teach us, it<br>teaches us a<br>lesson.”</span>
  </p>
  <span class="author" style="left:72px;top:636px">- Harold Quenby</span>

  <!-- Walt Prisco -->
  <div class="block umber" style="left:243px;top:195px;width:205px;height:361px"></div>
  <svg class="portrait" style="left:240px;top:561px" width="198" height="190" role="img" aria-label="Greyscale portrait photo of Walt Prisco">
    <defs><linearGradient id="g2" x1="0" y1="0" x2="0" y2="1"><stop offset="0" stop-color="#5d5d5d"/><stop offset="1" stop-color="#1e1e1e"/></linearGradient></defs>
    <rect width="198" height="190" fill="url(#g2)"/>
  </svg>
  <div class="frame" style="left:224px;top:187px;width:217px;height:355px"></div>
  <span class="mark" style="left:256px;top:220px">//</span>
  <p class="quote" style="left:240px;top:250px;width:180px">
    &nbsp;&nbsp;&nbsp;I tackle every<br>big new problem<br>by asking two<br>questions:<br>
    <span class="big">Who</span> has dealt<br>with this problem<br>well?<br>
    <span style="display:block;height:8px"></span>
    And <span class="big">what</span> can<br>we learn from<br>them?”
  </p>
  <span class="author" style="left:290px;top:575px">- Walt Prisco</span>

  <!-- Ravindra Selvapathi -->
  <svg class="portrait" style="left:437px;top:561px" width="180" height="190" role="img" aria-label="Greyscale portrait photo of Ravindra Selvapathi">
    <defs><linearGradient id="g3" x1="0" y1="0" x2="0" y2="1"><stop offset="0" stop-color="#6e6e6e"/><stop offset="1" stop-color="#2b2b2b"/></linearGradient></defs>
    <rect width="180" height="190" fill="url(#g3)"/>
  </svg>
  <div class="frame" style="left:421px;top:110px;width:217px;height:644px"></div>
  <span class="mark" style="left:447px;top:130px">//</span>
  <p class="quote" style="left:440px;top:158px;width:180px">
    &nbsp;&nbsp;&nbsp;If we can really<br>understand the<br>problem, the<br>answer will come<br>out of it, because<br>the<br>
    <span class="huge">answer is<br>not separate<br>from the<br>problem.”</span>
  </p>
  <span class="author" style="left:452px;top:508px">- Ravindra Selvapathi</span>

  <!-- Rufus Pembrook -->
  <div class="block cocoa" style="left:633px;top:97px;width:168px;height:681px"></div>
  <svg class="portrait" style="left:605px;top:561px" width="188" height="191" role="img" aria-label="Sepia portrait photo of Rufus Pembrook">
    <defs><linearGradient id="g4" x1="0" y1="0" x2="0" y2="1"><stop offset="0" stop-color="#7a6552"/><stop offset="1" stop-color="#3a2f26"/></linearGradient></defs>
    <rect width="188" height="191" fill="url(#g4)"/>
  </svg>
  <div class="frame" style="left:621px;top:87px;width:165px;height:467px"></div>
  <span class="mark" style="left:698px;top:150px">//</span>
  <p class="quote" style="left:634px;top:210px;width:148px">
    <span class="huge">Inaction</span><br>breeds doubt<br>and fear.<br>
    <span class="huge">Action</span><br>breeds<br>confidence<br>and courage.”
  </p>
  <span class="author" style="left:650px;top:480px">- Rufus Pembrook</span>

  <!-- Ned Falco -->
  <div class="block slate" style="left:767px;top:32px;width:259px;height:524px"></div>
  <svg class="portrait" style="left:809px;top:561px" width="212" height="189" role="img" aria-label="Greyscale portrait photo of Ned Falco">
    <defs><linearGradient id="g5" x1="0" y1="0" x2="0" y2="1"><stop offset="0" stop-color="#5a5a5a"/><stop offset="1" stop-color="#1c1c1c"/></linearGradient></defs>
    <rect width="212" height="189" fill="url(#g5)"/>
  </svg>
  <div class="frame" style="left:771px;top:33px;width:255px;height:720px"></div>
  <span class="mark" style="left:843px;top:62px">//</span>
  <p class="quote" style="left:796px;top:80px;width:210px">
    <span class="huge">&nbsp;&nbsp;&nbsp;Success</span><br>
    <span style="display:block;height:6px"></span>
    is nothing more<br>than a few simple<br>disciplines, practiced<br>every day; while<br>
    <span class="huge">failure</span><br>is simply a few errors<br>in judgment,<br>repeated every day.<br>It is the<br>accumulative weight<br>of our disciplines<br>and our judgments<br>that leads us to<br>either fortune or<br>failure.”
  </p>
  <span class="author" style="left:862px;top:578px">- Ned Falco</span>

  <!-- Lyle Dorsey -->
  <div class="block moss" style="left:1023px;top:57px;width:157px;height:703px"></div>
  <svg class="portrait" style="left:1023px;top:590px" width="157" height="170" role="img" aria-label="Green-tinted portrait photo of Lyle Dorsey">
    <defs><linearGradient id="g6" x1="0" y1="0" x2="0" y2="1"><stop offset="0" stop-color="#7b8d6a"/><stop offset="1" stop-color="#2a3324"/></linearGradient></defs>
    <rect width="157" height="170" fill="url(#g6)"/>
  </svg>
  <div class="frame" style="left:1018px;top:57px;width:148px;height:488px"></div>
  <span class="mark" style="left:1060px;top:130px">//</span>
  <p class="quote" style="left:1020px;top:160px;width:168px">
    &nbsp;&nbsp;&nbsp;What’s<br>
    <span class="huge">the one<br>thing<br>you can<br>do,</span><br>such that by<br>doing it,<br>everything<br>else will be<br>easier or<br>unnecessary?<br>”
  </p>
  <span class="author" style="left:1055px;top:560px">- Lyle Dorsey</span>

</main>
</body>
</html>
```